Coastline Premier Retreats Business Card Design

Design a business card for Coastline Premier Retreats. Look at the website for colors and reference. Card should have logo, name, title, office number, mobile number, email, URL and a tagline like, "Luxury Hotel & Resort Email Marketing" (This might change).

https://www.coastlinepremierretreats.example

The rest I will leave up to your imagination.

Contact Information for Business Card

Logo, name, title, office number, mobile number, email, URL and a tagline like, "Luxury Hotel & Resort Email Marketing" (This might change).

```html
<!DOCTYPE html>
<html lang="en">
<head>
<meta charset="utf-8">
<title>Coastline Premier Retreats — Business Card</title>
<link rel="stylesheet" href="https://fonts.googleapis.com/css2?family=Open+Sans:wght@400;700&family=Michroma&display=swap">
<style>
  :root {
    --stage: #3a3a3a;
    --card: #1c1c1c;
    --card-deep: #141414;
    --orange: #f47a20;
    --white: #f2f2f2;
    --muted: #d6d6d6;
  }
  html, body {
    margin: 0;
    padding: 0;
    width: 1200px;
    height: 801px;
    overflow: hidden;
    background: var(--stage);
    font-family: "Open Sans", Arial, sans-serif;
  }
  .stage {
    position: relative;
    width: 1200px;
    height: 801px;
    display: flex;
    align-items: center;
    justify-content: center;
    gap: 40px;
  }
  .card {
    position: relative;
    width: 540px;
    height: 309px;
    background: var(--card);
    border-bottom: 3px solid var(--orange);
    box-shadow: 0 10px 24px rgba(0,0,0,0.35);
    overflow: hidden;
  }

  /* Front */
  .brand {
    position: absolute;
    left: 34px;
    top: 124px;
    display: flex;
    align-items: center;
    gap: 10px;
  }
  .brand-mark {
    width: 14px;
    height: 14px;
    background: var(--orange);
    flex: none;
  }
  .brand-name {
    color: var(--white);
    font-weight: 700;
    font-size: 17px;
    line-height: 1.2;
    letter-spacing: 0.5px;
    text-transform: uppercase;
    width: 190px;
  }
  .divider {
    position: absolute;
    left: 250px;
    top: 52px;
    width: 2px;
    height: 136px;
    background: var(--orange);
  }
  .person {
    position: absolute;
    left: 266px;
    top: 50px;
    right: 16px;
    color: var(--white);
  }
  .person-name {
    margin: 0;
    color: var(--orange);
    font-weight: 700;
    font-size: 19px;
    letter-spacing: 0.3px;
    text-transform: uppercase;
  }
  .person-title {
    margin: 2px 0 14px;
    font-size: 13px;
    color: var(--muted);
  }
  .contact {
    list-style: none;
    margin: 0;
    padding: 0;
    font-size: 12px;
    color: var(--white);
  }
  .contact li {
    display: flex;
    align-items: center;
    gap: 7px;
    margin-bottom: 5px;
    white-space: nowrap;
  }
  .contact svg { width: 11px; height: 11px; flex: none; }
  .tagline-band {
    position: absolute;
    left: 0;
    right: 0;
    top: 230px;
    height: 44px;
    padding: 0 24px;
    box-sizing: border-box;
    background: var(--orange);
    display: flex;
    align-items: center;
    justify-content: center;
  }
  .tagline {
    margin: 0;
    font-family: "Michroma", Arial, sans-serif;
    font-size: 12px;
    line-height: 1;
    letter-spacing: 1.2px;
    white-space: nowrap;
    color: var(--card-deep);
    text-transform: uppercase;
  }

  /* Back */
  .back-pattern {
    position: absolute;
    inset: 0;
    background:
      radial-gradient(ellipse at 55% 40%, rgba(255,255,255,0.08), transparent 60%),
      linear-gradient(135deg, #161616 0%, #232323 55%, #1a1a1a 100%);
  }
  .back-brand {
    position: absolute;
    right: 90px;
    bottom: 62px;
    display: flex;
    align-items: center;
    gap: 8px;
    padding: 6px 10px;
    background: var(--card-deep);
  }
  .back-brand .brand-mark { width: 10px; height: 10px; }
  .back-brand .brand-name {
    width: auto;
    font-size: 12px;
    white-space: nowrap;
  }
</style>
</head>
<body>
<main class="stage">
  <section class="card card-front" aria-label="Business card front">
    <div class="brand">
      <span class="brand-mark"></span>
      <span class="brand-name">Coastline Premier Retreats</span>
    </div>
    <div class="divider"></div>
    <div class="person">
      <h1 class="person-name">Darren Holloway</h1>
      <p class="person-title">President / CEO</p>
      <ul class="contact">
        <li>
          <svg viewBox="0 0 12 12" aria-hidden="true"><path fill="#f47a20" d="M2.5 1h2l1 3-1.3 1a6 6 0 0 0 2.8 2.8l1-1.3 3 1v2a1 1 0 0 1-1 1A9 9 0 0 1 1.5 2a1 1 0 0 1 1-1z"/></svg>
          555.204.7319
        </li>
        <li>
          <svg viewBox="0 0 12 12" aria-hidden="true"><rect x="1" y="2.5" width="10" height="7" fill="#f47a20"/><path d="M1 2.5l5 4 5-4" fill="none" stroke="#1c1c1c" stroke-width="1"/></svg>
          info@coastlinepremierretreats.example
        </li>
        <li>
          <svg viewBox="0 0 12 12" aria-hidden="true"><circle cx="6" cy="6" r="5" fill="#f47a20"/><path d="M1 6h10M6 1c-2 2.7-2 7.3 0 10M6 1c2 2.7 2 7.3 0 10" fill="none" stroke="#1c1c1c" stroke-width="0.8"/></svg>
          www.coastlinepremierretreats.example
        </li>
      </ul>
    </div>
    <div class="tagline-band">
      <p class="tagline">Luxury Hotel &amp; Resort Email Marketing</p>
    </div>
  </section>

  <section class="card card-back" aria-label="Business card back">
    <div class="back-pattern" role="img" aria-label="Tonal repeating brand-name pattern in dark grey across the card back"></div>
    <div class="back-brand">
      <span class="brand-mark"></span>
      <span class="brand-name">Coastline Premier Retreats</span>
    </div>
  </section>
</main>
</body>
</html>
```